Pellham Grove Trust - New Website Designed

I need a site that looks like this http://www.quorlandgiving.org for boat donations. So please replace the cars with boats.

```html
<!DOCTYPE html>
<html lang="en">
<head>
<meta charset="utf-8">
<title>Pellham Grove Trust – Donate Your Boat</title>
<link rel="stylesheet" href="https://fonts.googleapis.com/css2?family=Open+Sans:wght@400;600;700;800&display=swap">
<style>
:root{
  --navy:#0f2a78;
  --navy-dark:#0b1d4f;
  --red:#a3171c;
  --red-dark:#7d0f13;
  --red-bright:#c0262b;
  --gold:#c9a75c;
  --grey-band:#dcdcde;
  --text:#2a2a2a;
  --muted:#555;
  --white:#fff;
  --line:#cfcfcf;
}
*{box-sizing:border-box;margin:0;padding:0}
html,body{width:1200px;height:2679px;overflow:hidden;background:#fff}
body{font-family:"Open Sans",Arial,sans-serif;color:var(--text);position:relative}
.abs{position:absolute}

/* header */
.site-header{left:0;top:0;width:1200px;height:157px;background:linear-gradient(90deg,#10183a 0%,#1f2b55 35%,#5a1a22 70%,#2a1c3a 100%)}
.brand{left:40px;top:52px;display:flex;align-items:center;gap:14px}
.brand-mark{width:34px;height:34px;border-radius:50%;background:var(--gold)}
.brand-name{font-size:30px;font-weight:800;color:var(--gold);letter-spacing:.5px}
.call-box{left:795px;top:0;width:375px;height:157px;background:var(--navy);display:flex;align-items:center;padding-left:22px;gap:14px;color:#fff}
.call-box .label{font-size:19px;font-weight:700;line-height:1}
.call-box .number{font-size:31px;font-weight:800;line-height:1.15}
.call-box .note{font-size:12px;font-weight:700}
.main-nav{left:0;top:157px;width:1200px;height:45px;background:var(--red);display:flex;align-items:center}
.main-nav a{position:absolute;color:#fff;font-size:15px;font-weight:700;text-decoration:none;letter-spacing:.3px}

/* hero */
.hero-photo{left:0;top:202px;width:1200px;height:396px;background:linear-gradient(120deg,#6d5b46 0%,#a99478 40%,#d9b98a 60%,#8a7d6c 100%)}
.form-tab{left:780px;top:157px;width:386px;height:48px;background:#fff;display:flex;align-items:center;justify-content:center;color:var(--red);font-size:18px;font-weight:800;box-shadow:0 2px 4px rgba(0,0,0,.25)}
.donate-form{left:795px;top:205px;width:357px;height:393px;background:var(--navy);padding:22px 18px 0}
.donate-form h3{color:#fff;font-size:16px;font-weight:700;text-align:center;margin-bottom:12px}
.field-row{display:flex;gap:6px;margin-bottom:8px}
.field{flex:1;height:29px;background:#fff;border-radius:2px;font-size:11px;color:#333;padding:7px 6px;display:flex;justify-content:space-between;align-items:center}
.field .caret{width:0;height:0;border-left:5px solid transparent;border-right:5px solid transparent;border-top:6px solid #444}
.btn-donate{display:block;margin:14px auto 0;width:156px;height:40px;background:var(--red);color:#fff;font-size:15px;font-weight:700;border:0;border-radius:3px;text-align:center;line-height:40px}

/* benefit band */
.benefit-band{left:0;top:598px;width:1200px;height:215px;background:linear-gradient(180deg,#e7e7e9,#cfd0d3)}
.benefit-flag{left:0;top:582px;width:536px;height:231px;background:linear-gradient(135deg,var(--red-bright),var(--red-dark));clip-path:polygon(0 0,92% 0,100% 100%,0 100%)}
.benefit-title{left:58px;top:628px;color:#fff;font-weight:800;font-size:27px;line-height:1.2}
.benefit-title .big{display:block;font-size:52px;color:var(--gold);letter-spacing:1px;line-height:1.15}
.benefit{top:640px;width:150px;text-align:center;color:var(--navy);font-size:12px;font-weight:700;line-height:1.3}
.benefit svg{display:block;margin:0 auto 12px}

/* section titles */
.section-title{width:1200px;left:0;text-align:center;font-size:29px;font-weight:800;color:var(--navy)}
.section-title span{color:var(--red)}
.section-title::before,.section-title::after{content:"";display:inline-block;width:112px;height:1px;background:var(--line);vertical-align:middle;margin:0 22px}

/* how to donate */
.step{top:947px;display:flex;gap:18px}
.step h4{color:var(--navy);font-size:15px;font-weight:800;line-height:1.3;margin:40px 0 10px}
.step p{font-size:13.5px;color:var(--muted);line-height:1.45}

/* why */
.why{left:0;top:1157px;width:1200px;height:415px;background:linear-gradient(100deg,#eeeeef 0%,#f5f3f1 35%,#e2ddd8 70%,#cfc8c1 100%)}
.why-list{left:140px;top:1291px;list-style:none}
.why-list li{display:flex;align-items:center;gap:10px;height:33px;font-size:13.5px;color:#333}
.why-list b{color:#1a1a1a}
.bullet{width:21px;height:21px;border-radius:50%;background:var(--red-dark);flex:none;display:flex;align-items:center;justify-content:center}

/* faq */
.faq-photo{left:80px;top:1706px;width:522px;height:425px;background:linear-gradient(160deg,#a3262c 0%,#c9c4c2 40%,#8a826f 70%,#6d6658 100%)}
.faq-list{left:634px;top:1706px;width:486px}
.faq-item{border:1px solid var(--line);border-radius:10px;height:40px;margin-bottom:7px;padding:0 14px;display:flex;justify-content:space-between;align-items:center;font-size:15px;font-weight:700;color:#333}
.faq-item.open{height:136px;flex-direction:column;align-items:stretch;justify-content:flex-start;padding-top:10px}
.faq-item.open .q{display:flex;justify-content:space-between}
.faq-item.open p{font-size:13px;font-weight:400;color:#555;line-height:1.45;margin-top:6px}
.chev{width:9px;height:9px;border-right:2px solid #444;border-bottom:2px solid #444;transform:rotate(45deg) translate(-2px,-2px)}
.chev.up{transform:rotate(-135deg)}

/* footer */
.site-footer{left:0;top:2188px;width:1200px;height:461px;background:linear-gradient(160deg,var(--red-bright) 0%,var(--red) 50%,var(--red-dark) 100%)}
.footer-tab{left:357px;top:2185px;width:473px;height:52px;background:var(--red-bright);border-radius:40px 40px 0 0}
.footer-brand{left:400px;top:2210px;display:flex;align-items:center;gap:12px}
.footer-brand .brand-mark{width:28px;height:28px}
.footer-brand .brand-name{font-size:24px}
.footer-col{top:2354px;color:#fff}
.footer-col h5{font-size:14px;font-weight:800;padding-bottom:10px;border-bottom:1px solid rgba(255,255,255,.6);margin-bottom:16px}
.footer-col p{font-size:12px;line-height:1.45;font-weight:600}
.footer-col a{display:block;color:#fff;font-size:13px;font-weight:600;text-decoration:none;line-height:1.4}
.badge{background:#e8e8e8;margin-bottom:12px}
.footer-call{left:779px;top:2357px;width:352px;height:150px;border:2px solid #fff;border-radius:6px;display:flex;align-items:center;padding-left:18px;gap:14px;color:#fff}
.footer-call .label{font-size:19px;font-weight:700;line-height:1}
.footer-call .number{font-size:31px;font-weight:800;line-height:1.15}
.footer-call .note{font-size:12px;font-weight:700}
.copyright{left:0;top:2649px;width:1200px;height:30px;text-align:center;font-size:11px;font-weight:700;color:#444;line-height:30px;background:#fff}
</style>
</head>
<body>

<header class="site-header abs">
  <div class="brand abs"><span class="brand-mark"></span><span class="brand-name">PELLHAM GROVE TRUST</span></div>
</header>
<div class="call-box abs">
  <svg width="62" height="62" viewBox="0 0 62 62"><circle cx="31" cy="31" r="28" fill="none" stroke="#fff" stroke-width="3"/><path d="M21 17c2-1 4 0 5 2l2 5c1 2 0 3-1 4l-2 2c2 4 5 7 9 9l2-2c1-1 2-2 4-1l5 2c2 1 3 3 2 5l-2 3c-2 2-5 2-8 1-9-3-16-10-19-19-1-3-1-6 1-8z" fill="#fff"/></svg>
  <div><div class="label">CALL TODAY TO DONATE</div><div class="number">1-800-555-0142</div><div class="note">Live Operators Available - 7 Days A Week</div></div>
</div>
<nav class="main-nav abs">
  <a href="#" style="left:178px">HOW TO DONATE</a>
  <a href="#" style="left:366px">WHY DONATE</a>
  <a href="#" style="left:523px">FAQ</a>
  <a href="#" style="left:609px">ABOUT</a>
</nav>

<div class="hero-photo abs" role="img" aria-label="A soldier in uniform embracing a child holding a small flag, in front of a marina with moored boats"></div>
<div class="form-tab abs">DONATE YOUR BOATS ONLINE</div>
<form class="donate-form abs">
  <h3>Full Tax Deduction - Running or Not</h3>
  <div class="field-row"><div class="field">First Name</div><div class="field">Last Name</div></div>
  <div class="field-row"><div class="field">Daytime Phone</div><div class="field">Email</div></div>
  <div class="field-row"><div class="field">Pickup Address</div></div>
  <div class="field-row"><div class="field">Pickup City</div></div>
  <div class="field-row"><div class="field">Pickup State<span class="caret"></span></div><div class="field">Zip Code</div></div>
  <div class="field-row"><div class="field">Choose Year<span class="caret"></span></div><div class="field">Choose Make<span class="caret"></span></div></div>
  <div class="field-row"><div class="field">Boat Model</div></div>
  <div class="btn-donate">DONATE NOW</div>
</form>

<div class="benefit-band abs"></div>
<div class="benefit-flag abs"></div>
<h2 class="benefit-title abs">DONATE YOUR BOATS TO<span class="big">VETERANS</span>MAKE A DIFFERENCE</h2>
<div class="benefit abs" style="left:554px">
  <svg width="60" height="56" viewBox="0 0 60 56"><circle cx="28" cy="28" r="24" fill="none" stroke="#a3171c" stroke-width="4"/><path d="M16 27l10 10 24-26" fill="none" stroke="#a3171c" stroke-width="5"/></svg>You have<br>no costs</div>
<div class="benefit abs" style="left:706px">
  <svg width="60" height="56" viewBox="0 0 60 56"><path d="M6 32h48l-7 10H12z M18 32v-8h18l6 8z M28 18h6v6h-6z" fill="#a3171c"/></svg>Free pickup,<br>running or not</div>
<div class="benefit abs" style="left:855px">
  <svg width="60" height="56" viewBox="0 0 60 56"><path d="M16 4h28v48l-5-4-4 4-5-4-5 4-4-4-5 4z" fill="none" stroke="#a3171c" stroke-width="3"/><path d="M22 14h16M22 22h16M22 38h16M30 26v12" stroke="#a3171c" stroke-width="2"/></svg>We issue you an<br>IRS tax receipt</div>
<div class="benefit abs" style="left:1008px">
  <svg width="60" height="56" viewBox="0 0 60 56"><rect x="22" y="6" width="28" height="38" fill="none" stroke="#a3171c" stroke-width="3"/><path d="M28 14h16M28 22h16M28 30h16" stroke="#a3171c" stroke-width="2"/><circle cx="18" cy="34" r="9" fill="none" stroke="#a3171c" stroke-width="3"/><path d="M11 41l-7 8" stroke="#a3171c" stroke-width="4"/></svg>We take care of<br>all paperwork.</div>

<h2 class="section-title abs" style="top:868px">HOW TO <span>DONATE</span></h2>
<div class="step abs" style="left:62px;width:360px">
  <svg width="80" height="100" viewBox="0 0 80 100"><path d="M18 8h36v12H18zM18 26h54v12H18zM18 44h54v12H18z" fill="#a3171c"/><path d="M6 54l20 8-6 4 10 12-4 4-10-12-4 6z" fill="#a3171c"/></svg>
  <div><h4>CALL US AT 1-800-555-0142 OR<br>FILL OUT THE ONLINE FORM</h4><p>Donating your boat is easy and<br>donation is accepted nationwide.</p></div>
</div>
<div class="step abs" style="left:444px;width:370px">
  <svg width="90" height="100" viewBox="0 0 90 100"><path d="M4 40h80l-10 14H14z M22 40V28h30l10 12z M36 18h8v10h-8z" fill="#a3171c"/></svg>
  <div><h4>WE PICK UP THE BOAT</h4><p>Any boats is accepted and we will<br>arrange to pick up your boat when<br>it is most convenient for you.</p></div>
</div>
<div class="step abs" style="left:846px;width:300px">
  <svg width="70" height="100" viewBox="0 0 70 100"><path d="M8 4h44v70l-7-5-7 5-8-5-7 5-8-5-7 5z" fill="none" stroke="#a3171c" stroke-width="3"/><path d="M16 14v66h46V14" fill="none" stroke="#a3171c" stroke-width="2"/><text x="30" y="50" font-family="Open Sans,Arial,sans-serif" font-size="26" font-weight="800" fill="#a3171c" text-anchor="middle">$</text></svg>
  <div><h4>TAX WRITE-OFF</h4><p>Once the boat donation is<br>complete, you will receive your<br>tax deductable boat donation<br>receipt.</p></div>
</div>

<section class="why abs" role="img" aria-label="Soft faded scene of soldiers raising a large flag at sunset"></section>
<h2 class="section-title abs" style="top:1212px">WHY DONATE <span>YOUR BOATS TO US</span></h2>
<ul class="why-list abs">
  <li><span class="bullet"><svg width="11" height="11" viewBox="0 0 11 11"><path d="M1 5.5h8M6 2l3.5 3.5L6 9" stroke="#fff" stroke-width="2" fill="none"/></svg></span><span><b>Civic Bureau A+ Rated &amp; IRS 501(c)3 Approved :</b> Free 24/7 Pickup with No DMV Hassles.</span></li>
  <li><span class="bullet"><svg width="11" height="11" viewBox="0 0 11 11"><path d="M1 5.5h8M6 2l3.5 3.5L6 9" stroke="#fff" stroke-width="2" fill="none"/></svg></span><span><b>Free Pick Up :</b> We will pick up your boat donation, running or not, when it's most convenient.</span></li>
  <li><span class="bullet"><svg width="11" height="11" viewBox="0 0 11 11"><path d="M1 5.5h8M6 2l3.5 3.5L6 9" stroke="#fff" stroke-width="2" fill="none"/></svg></span><span><b>All Boats Accepted :</b> We take your boat regardless of its condition or registration status.</span></li>
  <li><span class="bullet"><svg width="11" height="11" viewBox="0 0 11 11"><path d="M1 5.5h8M6 2l3.5 3.5L6 9" stroke="#fff" stroke-width="2" fill="none"/></svg></span><span><b>Income Tax Deduction :</b> We issue you an IRS tax receipt &amp; offer the largest resale network to get you the highest tax write-off possible.</span></li>
  <li><span class="bullet"><svg width="11" height="11" viewBox="0 0 11 11"><path d="M1 5.5h8M6 2l3.5 3.5L6 9" stroke="#fff" stroke-width="2" fill="none"/></svg></span><span><b>No Paperwork Hassles :</b> We take any boat and handle everything: DMV, Smog and IRS paperwork.</span></li>
  <li><span class="bullet"><svg width="11" height="11" viewBox="0 0 11 11"><path d="M1 5.5h8M6 2l3.5 3.5L6 9" stroke="#fff" stroke-width="2" fill="none"/></svg></span><span><b>Boat donations help fund programs :</b> And benefit Harborline Service Relief Fund. An IRS 501(c)3 nonprofit organization.</span></li>
  <li><span class="bullet"><svg width="11" height="11" viewBox="0 0 11 11"><path d="M1 5.5h8M6 2l3.5 3.5L6 9" stroke="#fff" stroke-width="2" fill="none"/></svg></span><span><b>Schedule a Free Pickup :</b> Complete the form and a representative will call you to arrange a convenient time to pickup your boat.</span></li>
</ul>

<h2 class="section-title abs" style="top:1627px">FREQUENTLY ASKED <span>QUESTIONS</span></h2>
<div class="faq-photo abs" role="img" aria-label="A flag waving over a column of marching soldiers' boots"></div>
<div class="faq-list abs">
  <div class="faq-item">What types of boats can be donated?<span class="chev"></span></div>
  <div class="faq-item open"><div class="q">What paperwork do I need to donate my boat?<span class="chev up"></span></div><p>All you need is a title, free of all liens. We will request some general information from you at the time of donation such as, the year, make, and model of the boat, as well as its general mechanical condition. We accept all boats, running or non-running.</p></div>
  <div class="faq-item">Is my donated boat tax -deductible?<span class="chev"></span></div>
  <div class="faq-item">What if the boat is not registered in my name?<span class="chev"></span></div>
  <div class="faq-item">How much will I receive as a tax deduction for my boat?<span class="chev"></span></div>
  <div class="faq-item">When will I receive my tax receipt?<span class="chev"></span></div>
  <div class="faq-item">How do I schedule a pick up?<span class="chev"></span></div>
</div>

<footer class="site-footer abs"></footer>
<div class="footer-tab abs"></div>
<div class="footer-brand abs"><span class="brand-mark"></span><span class="brand-name">PELLHAM GROVE TRUST</span></div>
<div class="footer-col abs" style="left:73px;width:238px">
  <h5>ABOUT PELLHAM GROVE TRUST</h5>
  <p>Lorem ipsum dolor sit amet, consectetuer adipiscing elit, sed diam nonummy nibheu ismod tincidunt ut laoreet dolore magna aliquam erat volutpat. Ut wisi enim ad mini veniam, quis nostrud exerci tation ullamcor per suscipit lobortis nisl ut aliquip ex ea co modo consequat.</p>
</div>
<div class="footer-col abs" style="left:380px;width:130px">
  <h5>NAVIGATION</h5>
  <a href="#">HOW TO DONATE</a><a href="#">WHY DONATE</a><a href="#">FAQ</a><a href="#">ABOUT</a>
</div>
<div class="footer-col abs" style="left:555px;width:160px">
  <h5>SAFE &amp; SECURE</h5>
  <div class="badge" style="width:160px;height:52px;border-radius:3px"></div>
  <div class="badge" style="width:110px;height:38px;border-radius:3px"></div>
  <div class="badge" style="width:40px;height:40px;border-radius:50%"></div>
</div>
<div class="footer-call abs">
  <svg width="62" height="62" viewBox="0 0 62 62"><circle cx="31" cy="31" r="28" fill="none" stroke="#fff" stroke-width="3"/><path d="M21 17c2-1 4 0 5 2l2 5c1 2 0 3-1 4l-2 2c2 4 5 7 9 9l2-2c1-1 2-2 4-1l5 2c2 1 3 3 2 5l-2 3c-2 2-5 2-8 1-9-3-16-10-19-19-1-3-1-6 1-8z" fill="#fff"/></svg>
  <div><div class="label">CALL TODAY TO DONATE</div><div class="number">1-800-555-0142</div><div class="note">Live Operators Available - 7 Days A Week</div></div>
</div>
<div class="copyright abs">COPYRIGHT © 2017 PELLHAM GROVE TRUST. PRIVACY POLICY I TERMS &amp; CONDITIONS. ALL RIGHTS RESERVED.</div>

</body>
</html>
```